New Business Card Design Project LORVANTI-Italy

we are LORVANTI-Italy
our company in the market for 3 years we are luxury cosmetic company and its about time for a facelift :)
i will like to have elegant luxurious and unique business card
that will give the person that get it a unique, luxurious and elegant impression
I'm VERY OPEN FOR NEW IDEAS , even duo i add a few files of things that i see on line and i like them

i add my logo as well
my website is LORVANTI.COM
(if you would like to see the main style that we have)

Target Market(s)

adult that have money :)

Industry/Entity Type

Business

Contact Information for Business Card

Name - Dario Lorvanti
Position - CEO and CO Founder
address - 4817 E Halvern
telephone - 555-384-1926
email - dario@lorvanti.com
fax - 555-384-1926
website - LORVANTI.COM

Colors
000000
959595
fbee3e
ffffff

Requirements
Must have
• big logo in GOLD color
• elegant look
• impressive
Nice to have
• not must but maybe classy pattern background
• not must but maybe emblem
• maybe clear plastic business card
Should not have
• colors
• images

```html
<!DOCTYPE html>
<html lang="en">
<head>
<meta charset="utf-8">
<title>LORVANTI Italy – Business Card</title>
<link href="https://fonts.googleapis.com/css2?family=Roboto:wght@400;500;700&display=swap" rel="stylesheet">
<style>
  :root {
    --stage: #2a2624;
    --card: #16181b;
    --card-edge: #1f2226;
    --gold: #d4ae3c;
    --white: #f4f4f4;
    --grey: #959595;
  }
  * { margin: 0; padding: 0; box-sizing: border-box; }
  html, body {
    width: 1200px; height: 769px; overflow: hidden;
    background: var(--stage);
    font-family: "Roboto", Arial, sans-serif;
  }
  .canvas {
    position: relative; width: 1200px; height: 769px;
    display: flex; align-items: center; justify-content: center; gap: 60px;
  }
  .card {
    position: relative; width: 500px; height: 286px;
    background: var(--card);
    border: 1px solid var(--card-edge);
    border-radius: 4px;
    box-shadow: 0 18px 40px rgba(0,0,0,.45);
  }

  /* Contact side */
  .card-front .emblem {
    position: absolute; top: 26px; right: 30px;
    width: 62px; height: 62px; border-radius: 50%;
    border: 3px solid var(--gold);
  }
  .card-front .address {
    position: absolute; right: 30px; top: 150px;
    display: flex; align-items: center; gap: 8px;
    color: var(--white); font-size: 14px;
  }
  .card-front .identity {
    position: absolute; left: 34px; bottom: 112px;
  }
  .name {
    color: var(--gold); font-weight: 700; font-size: 21px;
    letter-spacing: .3px; text-transform: uppercase;
  }
  .role { color: var(--white); font-size: 14px; margin-top: 3px; }
  .contacts {
    position: absolute; left: 34px; bottom: 22px;
    list-style: none;
  }
  .contacts li {
    display: flex; align-items: center; gap: 10px;
    color: var(--white); font-size: 14px; line-height: 22px;
  }
  .icon { width: 14px; height: 14px; flex: none; fill: var(--gold); }

  /* Brand side */
  .card-back {
    display: flex; flex-direction: column; align-items: center; justify-content: center;
  }
  .brand-mark {
    width: 84px; height: 84px; border-radius: 50%;
    border: 4px solid var(--gold); margin-bottom: 16px;
  }
  .brand-name {
    color: var(--gold); font-weight: 500; font-size: 40px;
    letter-spacing: 4px;
  }
  .brand-rule { width: 220px; height: 1px; background: var(--gold); margin: 8px 0 6px; opacity: .8; }
  .brand-tag { color: var(--gold); font-weight: 500; font-size: 12px; letter-spacing: 4px; }
</style>
</head>
<body>
<main class="canvas">

  <section class="card card-front" aria-label="Business card contact side">
    <div class="emblem" aria-hidden="true"></div>

    <p class="address">
      <span>4817 E Halvern</span>
      <svg class="icon" viewBox="0 0 16 16" aria-hidden="true"><path d="M8 0a5.5 5.5 0 0 0-5.5 5.5C2.5 10 8 16 8 16s5.5-6 5.5-10.5A5.5 5.5 0 0 0 8 0zm0 8a2.5 2.5 0 1 1 0-5 2.5 2.5 0 0 1 0 5z"/></svg>
    </p>

    <div class="identity">
      <h1 class="name">Dario Lorvanti</h1>
      <p class="role">CEO &amp; CO Founder</p>
    </div>

    <ul class="contacts">
      <li>
        <svg class="icon" viewBox="0 0 16 16" aria-hidden="true"><path d="M3.5 1 6 4 4.5 6a9 9 0 0 0 5.5 5.5L12 10l3 2.5-1.5 2.5C7 15 1 9 1 2.5z"/></svg>
        <span>555-384-1926</span>
      </li>
      <li>
        <svg class="icon" viewBox="0 0 16 16" aria-hidden="true"><path d="M4 1h7v4H4zM1 6h14v6h-2v3H3v-3H1zm4 5v3h6v-3z"/></svg>
        <span>555-384-1926</span>
      </li>
      <li>
        <svg class="icon" viewBox="0 0 16 16" aria-hidden="true"><path d="M1 3h14v10H1zm1.5 1.5v.3L8 9l5.5-4.2v-.3z"/></svg>
        <span>dario@lorvanti.com</span>
      </li>
      <li>
        <svg class="icon" viewBox="0 0 16 16" aria-hidden="true"><path d="M8 1a7 7 0 1 0 0 14A7 7 0 0 0 8 1zm-1 2.2v2.3L4.5 7 3 5.8A5 5 0 0 1 7 3.2zM9 13l1-3-2-1.5-2 1 1 3.5A5 5 0 0 0 9 13z"/></svg>
        <span>LORVANTI.COM</span>
      </li>
    </ul>
  </section>

  <section class="card card-back" aria-label="Business card brand side">
    <div class="brand-mark" aria-hidden="true"></div>
    <p class="brand-name">LORVANTI</p>
    <div class="brand-rule" aria-hidden="true"></div>
    <p class="brand-tag">ITALY</p>
  </section>

</main>
</body>
</html>
```